Business Card Design For A Renovation Contractor Company

We need a business card for a new company based in Singapore, our company name is "RB Tolvane". We are a renovation contractor that builds designs into reality. We build more of F&B restaurants, retail stores and commercial offices. We work very closely with designers. The final design should communicate to our client that we are a company that you can trust, that will plan and complete your project without giving you a headache. I like my client to remember my company as "RB". The beauty of SIMPLE is important.

Industry/Entity Type

Contractor

Requirements
Nice to have
• Black or Red base

```html
<!DOCTYPE html>
<html lang="en">
<head>
<meta charset="utf-8">
<title>RB Tolvane — Business Card</title>
<link rel="stylesheet" href="https://fonts.googleapis.com/css2?family=Source+Sans+3:wght@400;600;700&display=swap">
<style>
  :root {
    --brand-red: #ec1c2a;
    --ink-black: #1a1a1a;
    --band-dark: #2b2b2b;
    --paper-white: #ffffff;
    --text-grey: #3c3c3c;
    --backdrop: #e9e7e4;
    --card-w: 540px;
    --card-h: 309px;
  }
  * { box-sizing: border-box; margin: 0; padding: 0; }
  html, body {
    width: 1200px;
    height: 720px;
    overflow: hidden;
    background: var(--backdrop);
    font-family: "Source Sans 3", Arial, sans-serif;
  }
  .canvas {
    position: relative;
    width: 1200px;
    height: 720px;
    display: flex;
    align-items: center;
    justify-content: center;
    gap: 40px;
  }
  .card {
    position: relative;
    width: var(--card-w);
    height: var(--card-h);
    overflow: hidden;
    box-shadow: 0 6px 18px rgba(0,0,0,0.18);
  }

  /* Front card */
  .card-front { background: var(--brand-red); }
  .card-front .shapes { position: absolute; inset: 0; }
  .identity {
    position: absolute;
    left: 40px;
    top: 56px;
  }
  .brand-mark {
    display: flex;
    align-items: center;
    gap: 10px;
  }
  .brand-dot {
    width: 26px;
    height: 26px;
    border-radius: 50%;
    background: var(--brand-red);
  }
  .brand-name {
    font-size: 44px;
    font-weight: 400;
    line-height: 1;
    color: var(--ink-black);
    letter-spacing: -0.5px;
  }
  .tagline {
    margin-top: 6px;
    padding-top: 3px;
    border-top: 1.5px solid var(--ink-black);
    font-size: 15px;
    letter-spacing: 1.2px;
    color: var(--ink-black);
    width: 260px;
  }
  .person {
    position: absolute;
    left: 40px;
    top: 170px;
  }
  .person-name {
    font-size: 19px;
    font-weight: 700;
    color: var(--ink-black);
    line-height: 1.1;
  }
  .person-title {
    font-size: 13px;
    color: var(--brand-red);
    margin-bottom: 14px;
  }
  .address {
    font-size: 13px;
    line-height: 1.45;
    color: var(--text-grey);
  }
  .contacts {
    position: absolute;
    right: 24px;
    top: 140px;
    list-style: none;
    color: var(--paper-white);
    font-size: 12px;
  }
  .contacts li {
    display: flex;
    align-items: center;
    justify-content: flex-end;
    gap: 6px;
    line-height: 1.6;
  }
  .contacts svg { width: 11px; height: 11px; flex: none; }

  /* Back card */
  .card-back {
    background: var(--brand-red);
    display: flex;
    flex-direction: column;
    align-items: center;
  }
  .back-mark {
    margin-top: 108px;
    display: flex;
    align-items: center;
    gap: 16px;
  }
  .back-ring {
    width: 44px;
    height: 44px;
    border: 7px solid var(--ink-black);
    border-radius: 50%;
  }
  .back-name {
    font-size: 54px;
    font-weight: 700;
    color: var(--ink-black);
    line-height: 1;
  }
  .back-web {
    position: absolute;
    bottom: 30px;
    width: 100%;
    text-align: center;
    font-size: 16px;
    letter-spacing: 4px;
    color: var(--paper-white);
  }
</style>
</head>
<body>
<main class="canvas">

  <section class="card card-front" aria-label="Business card front">
    <svg class="shapes" viewBox="0 0 540 309" preserveAspectRatio="none" aria-hidden="true">
      <path d="M0 0 L440 0 C450 60 360 170 280 309 L0 309 Z" fill="var(--band-dark)"/>
      <path d="M0 0 L385 0 C395 60 305 170 225 309 L0 309 Z" fill="var(--paper-white)"/>
    </svg>

    <div class="identity">
      <div class="brand-mark">
        <span class="brand-dot"></span>
        <span class="brand-name">RB Tolvane</span>
      </div>
      <p class="tagline">turning plans into places</p>
    </div>

    <div class="person">
      <p class="person-name">Your Name</p>
      <p class="person-title">Title</p>
      <p class="address">Street Name, City Name<br>State Zip Code</p>
    </div>

    <ul class="contacts">
      <li>
        <svg viewBox="0 0 12 12"><circle cx="6" cy="6" r="6" fill="#fff"/><path d="M3.5 3.2l1.2-.4.8 1.6-.7.6c.3.8.9 1.4 1.7 1.7l.6-.7 1.6.8-.4 1.2c-2.6 0-4.8-2.2-4.8-4.8z" fill="var(--brand-red)"/></svg>
        +65 6210 4387
      </li>
      <li>
        <svg viewBox="0 0 12 12"><rect x="3" y="0.5" width="6" height="11" rx="1.2" fill="#fff"/><rect x="4" y="2" width="4" height="6" fill="var(--brand-red)"/></svg>
        +65 9134 2268
      </li>
      <li>
        <svg viewBox="0 0 12 12"><circle cx="6" cy="6" r="6" fill="#fff"/><rect x="2.8" y="3.8" width="6.4" height="4.4" fill="var(--brand-red)"/><path d="M2.8 3.8L6 6.4 9.2 3.8" stroke="#fff" stroke-width="0.8" fill="none"/></svg>
        info@rbtolvane.com
      </li>
      <li>
        <svg viewBox="0 0 12 12"><circle cx="6" cy="6" r="6" fill="#fff"/><circle cx="6" cy="6" r="3.4" fill="none" stroke="var(--brand-red)" stroke-width="0.9"/><path d="M2.6 6h6.8M6 2.6v6.8" stroke="var(--brand-red)" stroke-width="0.8"/></svg>
        www.rbtolvane.com
      </li>
    </ul>
  </section>

  <section class="card card-back" aria-label="Business card back">
    <div class="back-mark">
      <span class="back-ring"></span>
      <span class="back-name">RB Tolvane</span>
    </div>
    <p class="back-web">www.rbtolvane.com</p>
  </section>

</main>
</body>
</html>
```